New Business Card Design for Manufacturing

We are an engineering/manufacturing company that offers Advanced machining/assembly/engineering services, as well as innovative products for the heavy duty engine cooling markets.

We are looking to get a new business card designed that is clean and modern looking, but still fits the wide range of technical/skilled work we do.

- We hope to use this design as the base for other design work in new Presentations, web, and print work.

Industry/Entity Type

Engineering

Contact Information for Business Card

Our preferred color of blue is (RGB) 22/71/159 but can vary slightly from that color. Our content will be our Logo and full company name (Vantrell Forge Works, Inc.), company address, name, job title, phone number with extension, cell number, fax number, website, and email address on the cards.
We'd like the full company name next to the logo, but we are open to other interpretations of that layout.
Preferably, we would like the back side to be clean with just our logo, and the front to contain all of the contact information.

Colors
2f74b4
0355a3
85abd2

Requirements
Must have
• - Logo, company name, needed content - We are open to interpretation beyond that.
• - Standard size business card.
• - Horizontal orientation.
• - Enough space for lengthy names / job titles (for example, a job title could read "Directory of Human Resources" or "V.P. of Governmental Affairs"). We need this to look clean, whether the title be short (CEO) or long (as described above).

```html
<!DOCTYPE html>
<html lang="en">
<head>
<meta charset="utf-8">
<title>Vantrell Forge Works – Business Card</title>
<link rel="stylesheet" href="https://fonts.googleapis.com/css2?family=Open+Sans:ital,wght@0,400;0,700;1,800&family=Signika:wght@500&display=swap">
<style>
  :root {
    --brand-blue: #16479f;
    --deep-blue: #0355a3;
    --mid-blue: #2f74b4;
    --light-blue: #85abd2;
    --ink: #3a3d42;
    --card: #eef0f1;
    --band-grey: #a9adb1;
    --page: #d9d6d2;
    --tagline: #dfe3e8;
  }
  * { box-sizing: border-box; margin: 0; padding: 0; }
  html, body { width: 1200px; height: 1047px; overflow: hidden; }
  body {
    background: var(--page);
    font-family: "Open Sans", sans-serif;
    position: relative;
  }
  .card {
    position: absolute;
    left: 150px; top: 255px;
    width: 900px; height: 536px;
    background: var(--card);
    overflow: hidden;
    box-shadow: 0 6px 24px rgba(0,0,0,.18);
  }
  .company {
    position: absolute;
    left: 45px; top: 205px;
    width: 410px;
    color: var(--brand-blue);
    font-weight: 700;
    font-size: 38px;
    line-height: 1.15;
    text-transform: uppercase;
    letter-spacing: 0.5px;
  }
  .person {
    position: absolute;
    left: 500px; top: 82px;
  }
  .person-name {
    font-family: "Signika", sans-serif;
    font-weight: 500;
    font-size: 37px;
    color: var(--brand-blue);
    line-height: 1.1;
  }
  .person-title {
    font-size: 21px;
    color: var(--ink);
    margin-top: 4px;
  }
  .contact-list {
    position: absolute;
    left: 508px; top: 186px;
    list-style: none;
  }
  .contact-list li {
    display: flex;
    align-items: center;
    height: 32px;
    font-size: 22px;
    color: var(--ink);
  }
  .contact-list svg {
    width: 18px; height: 18px;
    margin-right: 16px;
    fill: var(--ink);
    flex: none;
  }
  .address {
    position: absolute;
    left: 500px; top: 360px;
    font-size: 22px;
    line-height: 32px;
    color: var(--ink);
  }
  .band {
    position: absolute;
    left: 0; bottom: 0;
    width: 900px; height: 66px;
  }
  .tagline {
    position: absolute;
    right: 42px; bottom: 15px;
    font-weight: 800;
    font-style: italic;
    font-size: 23px;
    letter-spacing: 0.5px;
    color: var(--tagline);
  }
</style>
</head>
<body>
  <article class="card">
    <div class="company">Vantrell Forge<br>Works, Inc.</div>

    <div class="person">
      <h1 class="person-name">John Doe Smith</h1>
      <p class="person-title">Managing Director</p>
    </div>

    <ul class="contact-list">
      <li>
        <svg viewBox="0 0 20 20" aria-hidden="true"><path d="M2 6c0-2 3-3 8-3s8 1 8 3v2h-4V6.5c-1-.4-2.5-.5-4-.5s-3 .1-4 .5V8H2z"/><path d="M4 9h12l1 8H3z"/></svg>
        111-2222-2222 (VANTRELL)
      </li>
      <li>
        <svg viewBox="0 0 20 20" aria-hidden="true"><path d="M5 1h10v18H5z M7 3v11h6V3z"/></svg>
        333-3333-3333
      </li>
      <li>
        <svg viewBox="0 0 20 20" aria-hidden="true"><path d="M5 2h10v5H5z M2 8h16v7h-3v3H5v-3H2z M7 13v3h6v-3z"/></svg>
        444-4444-4444
      </li>
      <li>
        <svg viewBox="0 0 20 20" aria-hidden="true"><path d="M1 4h18v12H1z M3 6l7 5 7-5v-.5H3z" fill-rule="evenodd"/></svg>
        www.yourwebsite.com
      </li>
      <li>
        <svg viewBox="0 0 20 20" aria-hidden="true"><circle cx="10" cy="10" r="9"/><path d="M1 10h18M10 1c3 3 3 15 0 18M10 1c-3 3-3 15 0 18" stroke="var(--card)" stroke-width="1.4" fill="none"/></svg>
        johndoe@yourwebsite.com
      </li>
    </ul>

    <p class="address">234 Anywhere St., Any City,<br>Any Town, US 123456</p>

    <svg class="band" viewBox="0 0 900 66" preserveAspectRatio="none" aria-hidden="true">
      <rect x="0" y="44" width="900" height="22" fill="var(--band-grey)"/>
      <polygon points="466,0 900,0 900,66 432,66" fill="var(--deep-blue)"/>
    </svg>
    <p class="tagline">FORGING WHAT'S NEXT</p>
  </article>
</body>
</html>
```